International Clinical Software Company needs a new business card design

We are looking for a new business card design for our company that has recently expanded into the UK market, making us a multinational company.
After having rebranded our website and produced a new style guide, we are looking for a business card that is creative and attention grabbing, while being consistent with the style and colour scheme used on the new website, www.plumvora.example
We produce care management technology for the aged care market, but the main aspect we aim to communicate is the human element of our software, and the way it assists in providing better care for aged people, and stronger relationships between aged people and the staff that care for them.
Our current business card is a dark green with gold text, which makes the text quite difficult to read, not very aesthetically appealing and the colour scheme looks quite dated.
We would like something fresh and modern, that can still be colourful but doesn't use large blocks of dark colour, and uses the colours within our logo.
Something tying in with the leaves that are used in our logo could work quite nicely, along with the Autumn/Fall colours of soft greens, yellows and reds (also in our existing logo). However also happy to look at fresh, completely out of the box ideas we may not have yet considered.
Target Market(s)
The people that receive this business card work in the aged card or health industry and are either corporate/management level staff or clinical (Registered Nurses, care workers etc.)
Industry/Entity Type
Health Product
Contact Information for Business Card
Company Name - BrindlewayCare
Company locations: United Kingdom, Australia, New Zealand
Staff Details:
Staff name: Derek Mallow
Staff job title: Executive Chairman
Staff email: d.mallow@plumvora.example
Office phone number: 01742 918576
Font styles to use
Other font styles liked:
- Calibri
Requirements
Must have
- Must include the BrindlewayCare brand name in it's current font
- Must include logo (3 leaves in gold circle)
- Must include Business Card Details
Nice to have
- Elements of gold
- White space
- Something autumn themed but not too cliched
Should not have
- No blue - used by a major competitor and we would like to differentiate from them
- Large blocks of dark green colour (the green that appears in our leaves on the logo on our current business card is the background colour and it is far too dark)

```html
<!DOCTYPE html>
<html lang="en">
<head>
<meta charset="utf-8">
<title>BrindlewayCare Business Card</title>
<link rel="stylesheet" href="https://fonts.googleapis.com/css2?family=Open+Sans:wght@400;600;700&display=swap">
<style>
  :root {
    --backdrop: #d9d9d7;
    --card-black: #0d0d0d;
    --card-black-soft: #1a1a1a;
    --gold: #bfae84;
    --white: #f4f4f2;
    --rule: #2a2a2a;
  }
  * { margin: 0; padding: 0; box-sizing: border-box; }
  html, body {
    width: 1200px;
    height: 900px;
    overflow: hidden;
    background: var(--backdrop);
    font-family: "Open Sans", Calibri, sans-serif;
  }
  .canvas {
    width: 1200px;
    height: 900px;
    display: flex;
    flex-direction: column;
    align-items: center;
    justify-content: center;
    gap: 40px;
  }
  .card {
    position: relative;
    width: 720px;
    height: 400px;
    border-radius: 4px;
    background: radial-gradient(ellipse at 40% 30%, var(--card-black-soft), var(--card-black) 75%);
    box-shadow: 0 6px 18px rgba(0,0,0,0.25);
    overflow: hidden;
  }

  /* Front */
  .card-front .brand {
    position: absolute;
    inset: 0;
    display: flex;
    align-items: center;
    justify-content: center;
    gap: 26px;
  }
  .brand-dot {
    flex: none;
    width: 150px;
    height: 150px;
    border-radius: 50%;
    background: var(--white);
  }
  .card-front .brand-name {
    font-size: 58px;
    font-weight: 400;
    color: var(--white);
    white-space: nowrap;
  }

  /* Back */
  .card-back .brand {
    position: absolute;
    right: 70px;
    top: 62px;
    display: flex;
    align-items: center;
    gap: 14px;
  }
  .card-back .brand-dot {
    width: 92px;
    height: 92px;
    background: var(--gold);
  }
  .card-back .brand-name {
    font-size: 32px;
    font-weight: 400;
    color: var(--gold);
    white-space: nowrap;
  }
  .person {
    position: absolute;
    left: 46px;
    top: 178px;
  }
  .person-name {
    font-size: 21px;
    font-weight: 700;
    color: var(--gold);
    line-height: 1.1;
  }
  .person-title {
    font-size: 17px;
    font-weight: 400;
    color: var(--white);
    margin-top: 2px;
  }
  .divider {
    position: absolute;
    left: 240px;
    right: 70px;
    top: 218px;
    height: 1px;
    background: var(--rule);
  }
  .contact {
    position: absolute;
    right: 70px;
    top: 244px;
    text-align: right;
    color: var(--white);
    font-size: 17px;
    line-height: 1.35;
  }
  .contact-line {
    display: flex;
    align-items: center;
    justify-content: flex-end;
    gap: 10px;
    margin-bottom: 6px;
  }
  .contact-line svg { width: 15px; height: 15px; }
  .contact-locations { font-size: 18px; margin-top: 8px; }
</style>
</head>
<body>
<main class="canvas">
  <section class="card card-front" aria-label="Business card front">
    <div class="brand">
      <span class="brand-dot"></span>
      <span class="brand-name">BrindlewayCare</span>
    </div>
  </section>

  <section class="card card-back" aria-label="Business card back">
    <div class="brand">
      <span class="brand-dot"></span>
      <span class="brand-name">BrindlewayCare</span>
    </div>
    <div class="person">
      <p class="person-name">Derek Mallow</p>
      <p class="person-title">Executive Chairman</p>
    </div>
    <div class="divider"></div>
    <div class="contact">
      <p class="contact-line contact-email">d.mallow@plumvora.example</p>
      <p class="contact-line contact-phone">
        <span>01742 918576</span>
        <svg viewBox="0 0 24 24" aria-hidden="true">
          <path fill="#bfae84" d="M6.6 10.8c1.4 2.8 3.8 5.1 6.6 6.6l2.2-2.2c.3-.3.7-.4 1-.2 1.1.4 2.3.6 3.6.6.6 0 1 .4 1 1V20c0 .6-.4 1-1 1C10.6 21 3 13.4 3 4c0-.6.4-1 1-1h3.5c.6 0 1 .4 1 1 0 1.3.2 2.5.6 3.6.1.3 0 .7-.2 1l-2.3 2.2z"/>
        </svg>
      </p>
      <p class="contact-locations">United Kingdom, Australia<br>New Zealand</p>
    </div>
  </section>
</main>
</body>
</html>
```